UI/ UX Design for ERP Software

We need a new UX/UI interface for a ERP software for property managers. Our CMMS / ERP solution is made based on responsive design technologies and is coded in PHP.
The overall UX to be similar to Tev Ulna - easy navigation, intuitive menus.

Industry/Entity Type

Property Management

Number of Pages Required

5+ page

Requirements
Must have
• Round dock buttons
Consistent icons across the application
Enough Spacing between buttons/icons/ menu
Consistent Font
Nice to have
• We would like the UX to allow the users to use the application without /minimum training.
Should not have
• we don't want anything that is classic with respect to UX

```html
<!DOCTYPE html>
<html lang="en">
<head>
<meta charset="utf-8">
<title>Nestora – Active Dashboard</title>
<link href="https://fonts.googleapis.com/css2?family=Roboto:wght@400;500;700&family=Poppins:wght@600&display=swap" rel="stylesheet">
<style>
:root{
  --page:#f3f3f8;
  --white:#ffffff;
  --ink:#2b2f3a;
  --muted:#5d6270;
  --blue:#0b7be8;
  --band-a:#0a63ee;
  --band-b:#18c6ef;
  --grid:#e3e5ea;
  --yellow:#e3d23e;
  --purple:#7d78e6;
  --sky:#72b2ea;
  --orange:#f59a4a;
  --dark:#3a3a3a;
  --green:#84e36c;
  --red:#ea5277;
}
*{box-sizing:border-box;margin:0;padding:0}
html,body{width:1200px;height:589px;overflow:hidden}
body{background:var(--page);font-family:"Roboto",sans-serif;color:var(--ink);position:relative}
.topbar{position:absolute;left:0;top:0;width:1200px;height:62px;background:var(--white)}
.brand{position:absolute;left:40px;top:18px;display:flex;align-items:center;gap:8px;font:700 24px "Roboto",sans-serif;color:var(--blue)}
.brand-mark{width:22px;height:22px;border-radius:4px;background:var(--blue)}
.nav{position:absolute;left:245px;top:22px;display:flex;gap:25px;font-size:11px;color:var(--muted);font-weight:500}
.nav span{display:flex;align-items:center;gap:5px}
.nav i{width:9px;height:9px;border-radius:2px;background:var(--muted);display:inline-block}
.user{position:absolute;left:1055px;top:18px;display:flex;align-items:center;gap:8px;font-size:10px;font-weight:500}
.bell{width:12px;height:12px;border-radius:50%;background:var(--blue);margin-right:18px}
.avatar{width:27px;height:27px;border-radius:50%;background:linear-gradient(#c9b8a4,#6f625a)}
.card{position:absolute;left:20px;top:97px;width:1160px;height:441px;background:var(--white);border-radius:18px}
.band{position:absolute;left:29px;top:105px;width:1142px;height:102px;border-radius:14px;background:linear-gradient(100deg,var(--band-a),#1190ef 55%,var(--band-b));color:var(--white)}
.band-title{position:absolute;left:20px;top:21px;font:600 14px "Poppins",sans-serif;display:flex;gap:8px;align-items:center}
.stat{position:absolute;top:23px;display:flex;gap:10px;align-items:flex-start}
.stat .dot{width:29px;height:29px;border-radius:50%;background:var(--white);display:flex;align-items:center;justify-content:center}
.stat b{display:block;font-size:11px;font-weight:700;margin-top:1px}
.stat small{display:block;font-size:10px;margin-top:3px}
.tabs{position:absolute;left:0;top:71px;height:31px;display:flex;align-items:center;font-size:10px;font-weight:500}
.tab{margin-left:20px;display:flex;gap:4px;align-items:center}
.tab.active{background:var(--white);color:var(--blue);height:31px;padding:0 27px;margin-left:16px;border-radius:10px 10px 0 0;font-size:11px}
.cal{width:8px;height:8px;border:1.2px solid currentColor;border-radius:1px}
.chart-title{position:absolute;left:519px;top:231px;font-size:12px;font-weight:500;color:var(--blue);display:flex;gap:5px;align-items:center}
.chart{position:absolute;left:0;top:0}
.chart text{font-family:"Roboto",sans-serif;font-size:10px}
</style>
</head>
<body>
<header class="topbar">
  <div class="brand"><span class="brand-mark"></span>Nestora</div>
  <nav class="nav">
    <span><i></i>Dashboard</span><span><i></i>Customers</span><span><i></i>Properties</span><span><i></i>Tenants</span><span><i></i>Contacts</span><span><i></i>Management ⌄</span><span><i></i>Pages ⌄</span><span><i></i>Settings</span>
  </nav>
  <div class="user"><span class="bell"></span><span class="avatar" role="img" aria-label="User profile photo"></span>Ravi Lund ⌄</div>
</header>

<section class="card"></section>
<section class="band">
  <div class="band-title">
    <svg width="12" height="11" viewBox="0 0 12 11"><path d="M6 0 12 5H10V11H7V7H5V11H2V5H0Z" fill="#fff"/></svg>Active Dashboard</div>
  <div class="stat" style="left:403px"><span class="dot"><svg width="12" height="11" viewBox="0 0 12 11"><path d="M6 0 12 5H10V11H2V5H0Z" fill="#0b7be8"/></svg></span><div><b>PROPERTIES</b><small>3</small></div></div>
  <div class="stat" style="left:541px"><span class="dot"><svg width="10" height="12" viewBox="0 0 10 12"><circle cx="5" cy="3" r="3" fill="#0b7be8"/><rect x="0" y="7" width="10" height="5" rx="2" fill="#0b7be8"/></svg></span><div><b>TENANTS</b><small>8</small></div></div>
  <div class="stat" style="left:650px"><span class="dot"><svg width="11" height="11" viewBox="0 0 11 11"><path d="M5.5 0V11M0 5.5H11" stroke="#0b7be8" stroke-width="2"/></svg></span><div><b>TOTAL PROPERTIES AREA</b><small>422,000.00 sq.ft</small></div></div>
  <div class="stat" style="left:853px"><span class="dot"><svg width="11" height="11" viewBox="0 0 11 11"><path d="M5.5 0V11M0 5.5H11" stroke="#0b7be8" stroke-width="2"/></svg></span><div><b>RENTED AREA</b><small>233,500.00 sq.ft.</small></div></div>
  <div class="stat" style="left:996px"><span class="dot"><svg width="11" height="11" viewBox="0 0 11 11"><path d="M5.5 0V11M0 5.5H11" stroke="#0b7be8" stroke-width="2"/></svg></span><div><b>VACANCIES AREA</b><small>188,500.00 sq.ft.</small></div></div>
  <div class="tabs">
    <span class="tab active"><i class="cal"></i>Last 7 days</span>
    <span class="tab"><i class="cal"></i>Last Months</span>
    <span class="tab"><i class="cal"></i>Last 3 Months</span>
    <span class="tab"><i class="cal"></i>Next 7 Days</span>
    <span class="tab" style="margin-left:26px"><i class="cal"></i>Next Months</span>
    <span class="tab"><i class="cal"></i>Next 3 Months</span>
  </div>
</section>

<div class="chart-title"><svg width="13" height="10" viewBox="0 0 13 10"><rect x="0" y="8" width="2" height="2" fill="#0b7be8"/><rect x="3.5" y="6" width="2" height="4" fill="#0b7be8"/><rect x="7" y="3" width="2" height="7" fill="#0b7be8"/><rect x="10.5" y="0" width="2" height="10" fill="#0b7be8"/></svg>12/27/2020 - 01/03/2021</div>

<svg class="chart" width="1200" height="589" viewBox="0 0 1200 589">
  <g stroke="var(--grid)" stroke-width="1">
    <line x1="103" y1="273" x2="1006" y2="273"/><line x1="103" y1="312" x2="1006" y2="312"/><line x1="103" y1="351" x2="1006" y2="351"/><line x1="103" y1="389" x2="1006" y2="389"/><line x1="103" y1="428" x2="1006" y2="428"/><line x1="103" y1="467" x2="1006" y2="467"/>
    <line x1="103" y1="467" x2="103" y2="485"/><line x1="216" y1="467" x2="216" y2="485"/><line x1="329" y1="467" x2="329" y2="485"/><line x1="442" y1="467" x2="442" y2="485"/><line x1="555" y1="467" x2="555" y2="485"/><line x1="667" y1="467" x2="667" y2="485"/><line x1="781" y1="467" x2="781" y2="485"/><line x1="894" y1="467" x2="894" y2="485"/><line x1="1006" y1="467" x2="1006" y2="485"/>
  </g>
  <g fill="var(--ink)" text-anchor="end" font-size="10">
    <text x="90" y="277">1.25</text><text x="90" y="316">1</text><text x="90" y="355">0.75</text><text x="90" y="393">0.5</text><text x="90" y="432">0.25</text><text x="90" y="471">0</text>
  </g>
  <g fill="var(--muted)" text-anchor="middle">
    <text x="161" y="491">12-27-2020</text><text x="273" y="491">12-28-2020</text><text x="386" y="491">12-29-2020</text><text x="497" y="491">12-30-2020</text><text x="610" y="491">12-31-2020</text><text x="723" y="491">01-01-2020</text><text x="836" y="491">01-02-2020</text><text x="948" y="491">01-03-2020</text>
  </g>
  <g fill="none" stroke-width="1.2">
    <polyline stroke="var(--yellow)" points="161,324 273,286 386,286 497,324 610,286 723,324 836,324 948,286"/>
    <polyline stroke="var(--purple)" points="161,350 273,312 386,312 497,350 610,312 723,350 836,350 948,312"/>
    <polyline stroke="var(--sky)" points="161,311 273,349 386,349 497,311 610,349 723,311 836,311 948,349"/>
    <polyline stroke="var(--orange)" points="161,416 273,379 386,379 497,416 610,378 723,416 836,416 948,378"/>
    <polyline stroke="var(--dark)" points="161,366 273,404 386,404 497,366 610,404 723,366 836,366 948,404"/>
    <polyline stroke="var(--green)" points="161,390 273,427 386,427 497,390 610,428 723,390 836,390 948,428"/>
    <polyline stroke="var(--red)" points="161,428 273,466 386,466 497,428 610,466 723,429 836,429 948,466"/>
  </g>
  <g r="5">
    <g fill="var(--yellow)"><circle cx="161" cy="324" r="5"/><circle cx="273" cy="286" r="5"/><circle cx="386" cy="286" r="5"/><circle cx="497" cy="324" r="5"/><circle cx="610" cy="286" r="5"/><circle cx="723" cy="324" r="5"/><circle cx="836" cy="324" r="5"/><circle cx="948" cy="286" r="5"/></g>
    <g fill="var(--purple)"><circle cx="161" cy="350" r="5"/><circle cx="273" cy="312" r="5"/><circle cx="386" cy="312" r="5"/><circle cx="497" cy="350" r="5"/><circle cx="610" cy="312" r="5"/><circle cx="723" cy="350" r="5"/><circle cx="836" cy="350" r="5"/><circle cx="948" cy="312" r="5"/></g>
    <g fill="var(--sky)"><circle cx="161" cy="311" r="5"/><circle cx="273" cy="349" r="5"/><circle cx="386" cy="349" r="5"/><circle cx="497" cy="311" r="5"/><circle cx="610" cy="349" r="5"/><circle cx="723" cy="311" r="5"/><circle cx="836" cy="311" r="5"/><circle cx="948" cy="349" r="5"/></g>
    <g fill="var(--orange)"><circle cx="161" cy="416" r="5"/><circle cx="273" cy="379" r="5"/><circle cx="386" cy="379" r="5"/><circle cx="497" cy="416" r="5"/><circle cx="610" cy="378" r="5"/><circle cx="723" cy="416" r="5"/><circle cx="836" cy="416" r="5"/><circle cx="948" cy="378" r="5"/></g>
    <g fill="var(--dark)"><circle cx="161" cy="366" r="5"/><circle cx="273" cy="404" r="5"/><circle cx="386" cy="404" r="5"/><circle cx="497" cy="366" r="5"/><circle cx="610" cy="404" r="5"/><circle cx="723" cy="366" r="5"/><circle cx="836" cy="366" r="5"/><circle cx="948" cy="404" r="5"/></g>
    <g fill="var(--green)"><circle cx="161" cy="390" r="5"/><circle cx="273" cy="427" r="5"/><circle cx="386" cy="427" r="5"/><circle cx="497" cy="390" r="5"/><circle cx="610" cy="428" r="5"/><circle cx="723" cy="390" r="5"/><circle cx="836" cy="390" r="5"/><circle cx="948" cy="428" r="5"/></g>
    <g fill="var(--red)"><circle cx="161" cy="428" r="5"/><circle cx="273" cy="466" r="5"/><circle cx="386" cy="466" r="5"/><circle cx="497" cy="428" r="5"/><circle cx="610" cy="466" r="5"/><circle cx="723" cy="429" r="5"/><circle cx="836" cy="429" r="5"/><circle cx="948" cy="466" r="5"/></g>
  </g>
  <g>
    <text x="962" y="290" fill="var(--yellow)">Completed Property Inspections</text>
    <text x="962" y="316" fill="var(--purple)">Completed Work Orders</text>
    <text x="962" y="353" fill="var(--sky)">Scheduled Maintenance</text>
    <text x="962" y="382" fill="var(--orange)">Future Scheduled Maintenance</text>
    <text x="962" y="408" fill="var(--dark)">Scheduled Work Orders</text>
    <text x="962" y="431" fill="var(--green)">Completed Scheduled Maintenance</text>
    <text x="962" y="470" fill="var(--red)">Property Inspections in Progress</text>
  </g>
</svg>
</body>
</html>
```